Brookvane Consulting Business Card Design

Business Card Design for Brookvane Consulting. Brookvane Consulting is a boutique consultancy based in Atlanta, GA., that specializes in marketing strategy, organization planning, and leadership development. We provide solutions for small businesses and startups as well as Vantage 300 companies.

http://brookvaneconsulting.com/

Target Market(s)

We provide solutions for small businesses and startups as well as Vantage 300 companies.

Industry/Entity Type

Consulting

Contact Information for Business Card

Two sided business card with priority on contact information, logo, tag line (Inspiration to Dream More, Do More, Become More)

Colors

Designer to choose colors to be used in the design.

Requirements
Must have
• contact information, logo, tag line (Inspiration to Dream More, Do More, Become More)
• Simple no over communication.
Nice to have
• I would like to see different placements of logo and creative use of both sides of the card
Should not have
• Do not put too much information on the card.

```html
<!DOCTYPE html>
<html lang="en">
<head>
<meta charset="utf-8">
<title>Brookvane Consulting Business Card</title>
<link rel="stylesheet" href="https://fonts.googleapis.com/css2?family=Roboto+Condensed:wght@400;700&family=Playfair+Display:ital,wght@1,700&display=swap">
<style>
  :root {
    --stage: #e9e6e1;
    --card-dark: #242424;
    --card-darker: #1c1c1c;
    --band: #ffffff;
    --ink-light: #ffffff;
    --ink-muted: #c9c9c9;
    --ink-dark: #1a1a1a;
  }
  * { margin: 0; padding: 0; box-sizing: border-box; }
  html, body { width: 1200px; height: 911px; overflow: hidden; }
  body {
    background: var(--stage);
    position: relative;
    font-family: "Roboto Condensed", sans-serif;
  }
  .card {
    position: absolute;
    top: 158px;
    width: 340px;
    height: 595px;
    overflow: hidden;
    box-shadow: 0 10px 28px rgba(0,0,0,0.28);
  }
  .card--front { left: 190px; background: var(--card-dark); }
  .card--back { left: 670px; background: var(--card-darker); }

  .tagline-band {
    position: absolute;
    left: 0; top: 0;
    width: 100%; height: 100px;
    background: var(--band);
    display: flex;
    align-items: center;
    justify-content: center;
    text-align: center;
  }
  .tagline {
    font-family: "Playfair Display", serif;
    font-style: italic;
    font-weight: 700;
    font-size: 17px;
    line-height: 1.3;
    color: var(--ink-dark);
  }

  .rotated {
    position: absolute;
    left: 0;
    transform-origin: 0 0;
    transform: rotate(-90deg);
  }
  .card--front .rotated { top: 595px; width: 495px; height: 340px; }
  .card--back .rotated { top: 595px; width: 595px; height: 340px; }

  .brand {
    display: flex;
    align-items: center;
    gap: 10px;
    color: var(--ink-light);
    font-weight: 700;
    white-space: nowrap;
  }
  .brand__mark { background: var(--ink-light); flex: none; }

  .front-content { position: absolute; left: 60px; top: 70px; }
  .front-content .brand { font-size: 34px; }
  .front-content .brand__mark { width: 14px; height: 14px; }

  .contact { margin-top: 48px; color: var(--ink-muted); }
  .contact__name {
    font-size: 19px;
    font-weight: 700;
    text-transform: uppercase;
    color: var(--ink-muted);
  }
  .contact__role { font-size: 17px; margin-bottom: 12px; }
  .contact__line {
    display: flex;
    align-items: center;
    gap: 10px;
    font-size: 15px;
    line-height: 1.6;
  }
  .contact__line svg { width: 12px; height: 12px; flex: none; }

  .back-pattern { position: absolute; inset: 0; background: var(--card-darker); }
  .back-content {
    position: absolute; inset: 0;
    display: flex; align-items: center; justify-content: center;
  }
  .back-content .brand { font-size: 40px; }
  .back-content .brand__mark { width: 16px; height: 16px; }
</style>
</head>
<body>
  <section class="card card--front" aria-label="Card front">
    <div class="tagline-band">
      <p class="tagline">Inspiration to Dream More<br>Do More, Become More</p>
    </div>
    <div class="rotated">
      <div class="front-content">
        <div class="brand"><span class="brand__mark"></span>Brookvane Consulting</div>
        <div class="contact">
          <p class="contact__name">Dorian Whitfield</p>
          <p class="contact__role">Founder/Managing Director</p>
          <p class="contact__line">
            <svg viewBox="0 0 12 12" aria-hidden="true"><path d="M2.5 1 L4.5 1 L5.2 3.6 L4 4.6 Q5 7 7.4 8 L8.4 6.8 L11 7.5 L11 9.5 Q10 11 8 10.8 Q2 9.5 1.2 3.6 Q1.2 1.6 2.5 1 Z" fill="#c9c9c9"/></svg>
            424-555-0172
          </p>
          <p class="contact__line">
            <svg viewBox="0 0 12 12" aria-hidden="true"><rect x="1" y="2.5" width="10" height="7" fill="#c9c9c9"/><path d="M1 2.5 L6 6.5 L11 2.5" stroke="#242424" fill="none"/></svg>
            dorian@brookvaneconsulting.com
          </p>
          <p class="contact__line">
            <svg viewBox="0 0 12 12" aria-hidden="true"><circle cx="6" cy="6" r="5" fill="#c9c9c9"/><path d="M1 6 H11 M6 1 Q3 6 6 11 M6 1 Q9 6 6 11" stroke="#242424" stroke-width="0.8" fill="none"/></svg>
            brookvaneconsulting.com
          </p>
        </div>
      </div>
    </div>
  </section>

  <section class="card card--back" aria-label="Card back">
    <div class="back-pattern" role="img" aria-label="Subtle dark geometric grid pattern background"></div>
    <div class="rotated">
      <div class="back-content">
        <div class="brand"><span class="brand__mark"></span>Brookvane Consulting</div>
      </div>
    </div>
  </section>
</body>
</html>
```